Vitamin B12 Liquid Drops Label

hi, i need a label designed for my vitamin b12 drops that i am going to be selling on shopzello. the label needs to quickly capture the attention of a buyer as he or she is scrolling through the thumbnail search results on shopzello.com my brand is called nralo. i already have an example brand logo i will be using, however, i need help designing the rest of the label. attached are some examples of labels i like for other supplements.some of these examples are pink. i do not want pink. please go for a blue/green color scheme. THE DESIGN MUST BE BOLD

Target Market(s)

adults ages 30 - 64

Font styles to use
Sans Serif

Colors
0455a3
cedeed
3176b5
85acd3
cfdeed
9bcb3b
abd037
cadf82
00a990

Requirements
Must have
• - bold design
• - somewhat gender-neutral color scheme because this will be used equally by men and women
• - B12 MUST be very prominent and visible on the label
Should not have
• - it should not be "crunchy" looking

```html
<!DOCTYPE html>
<html lang="en">
<head>
<meta charset="utf-8">
<title>Nralo Vitamin B12 Label</title>
<link rel="stylesheet" href="https://fonts.googleapis.com/css2?family=Open+Sans:wght@700;800&display=swap">
<style>
  :root {
    --backdrop: #cfdeed;
    --label-blue: #0455a3;
    --label-blue-deep: #044a8f;
    --band-green: #9bcb3b;
    --band-lime: #abd037;
    --ink-blue: #0455a3;
    --accent-light: #cadf82;
    --accent-green: #abd037;
  }
  * { margin: 0; padding: 0; box-sizing: border-box; }
  html, body {
    width: 1200px;
    height: 900px;
    overflow: hidden;
  }
  body {
    background: var(--backdrop);
    font-family: "Open Sans", Arial, sans-serif;
    position: relative;
  }
  .label {
    position: absolute;
    left: 330px;
    top: 108px;
    width: 540px;
    height: 684px;
    background: linear-gradient(180deg, var(--label-blue) 0%, var(--label-blue-deep) 100%);
    overflow: hidden;
  }
  .label-band {
    position: absolute;
    inset: 0;
    width: 100%;
    height: 100%;
  }
  .product-name {
    position: absolute;
    left: 20px;
    top: 292px;
    font-size: 56px;
    font-weight: 800;
    line-height: 1;
    color: var(--ink-blue);
    letter-spacing: 0.5px;
    white-space: nowrap;
  }
  .product-form {
    position: absolute;
    left: 26px;
    top: 384px;
    font-size: 15px;
    font-weight: 800;
    letter-spacing: 10px;
    color: var(--accent-light);
    white-space: nowrap;
  }
  .brand-name {
    position: absolute;
    right: 26px;
    bottom: 52px;
    font-size: 58px;
    font-weight: 800;
    line-height: 1;
    color: var(--accent-green);
    letter-spacing: 1px;
  }
</style>
</head>
<body>
  <main class="label" aria-label="Vitamin B12 drops label">
    <svg class="label-band" viewBox="0 0 540 684" preserveAspectRatio="none" aria-hidden="true">
      <defs>
        <linearGradient id="bandFill" x1="0" y1="0" x2="1" y2="1">
          <stop offset="0" stop-color="#abd037"/>
          <stop offset="1" stop-color="#9bcb3b"/>
        </linearGradient>
      </defs>
      <polygon points="0,0 540,0 410,364 0,364" fill="url(#bandFill)"/>
    </svg>
    <h1 class="product-name">VITAMIN B12</h1>
    <p class="product-form">METHYLCOBALAMIN</p>
    <p class="brand-name">NRALO</p>
  </main>
</body>
</html>
```